HOT TUB - SPAS service needs an business card

I need an business for my company who his specialise in a maintenance,water treatment and cleaning of Hot Tub - Spas for commercial and residential customers. The company operate mainly in the ski resort of Chamonix, Megève and St Gervais. The final product should communicate pure water, cleanest and professional for luxury property's.
I have upload a logo but any improvement on it is welcome.(color,size, details etc..) or any other idea. Thank you
Company Name: 58 BAINS
My name: Lucien Marchetti
Email: lucimarch@examplemail.net
Tel: +33 (0)6 71 58 29 64
Description to be on the card in french(first langage) and in English:
- Spas service
- Entretien, traitement eau, nettoyage.
- Maintenance, water treatment, cleaning.
Industry/Entity Type
Residential
Colors
Designer to choose colors to be used in the design.
Look and feel
Each slider illustrates characteristics of the customer's brand and the style your logo design should communicate.

```html
<!DOCTYPE html>
<html lang="fr">
<head>
<meta charset="utf-8">
<title>58 BAINS — Cartes de visite</title>
<link href="https://fonts.googleapis.com/css2?family=Exo+2:wght@300;400;500&display=swap" rel="stylesheet">
<style>
  :root {
    --brand-blue: #4f97c3;
    --brand-blue-soft: rgba(79, 151, 195, 0.55);
    --card-white: #ececec;
    --page-bg: #dcdcdc;
    --ink: #3a3a3a;
    --paper-text: #ffffff;
  }
  * { margin: 0; padding: 0; box-sizing: border-box; }
  html, body {
    width: 1200px; height: 1000px; overflow: hidden;
    background: var(--page-bg);
    font-family: "Exo 2", Arial, sans-serif;
  }
  .sheet {
    position: relative; width: 1200px; height: 1000px;
    display: flex; flex-direction: column; align-items: center;
    justify-content: center; gap: 40px;
  }
  .card {
    position: relative; width: 680px; height: 440px; overflow: hidden;
    box-shadow: 0 6px 18px rgba(0,0,0,0.18);
  }

  /* Front */
  .card--front { background: var(--brand-blue); display: flex; align-items: center; justify-content: center; }
  .brand-lockup { display: flex; align-items: center; gap: 16px; }
  .brand-dot { width: 22px; height: 22px; border-radius: 50%; background: var(--paper-text); }
  .brand-name {
    color: var(--paper-text); font-weight: 500; font-size: 54px; letter-spacing: 2px;
  }

  /* Back */
  .card--back { background: var(--card-white); }
  .back-brand {
    position: absolute; top: 30px; right: 34px; display: flex; align-items: center; gap: 8px;
  }
  .back-brand .brand-dot { width: 12px; height: 12px; background: var(--brand-blue); }
  .back-brand .brand-name { color: var(--brand-blue); font-size: 24px; letter-spacing: 1px; }

  .side-stripe {
    position: absolute; top: 170px; bottom: 0; width: 12px; background: var(--brand-blue-soft);
  }
  .side-stripe--one { left: 18px; }
  .side-stripe--two { left: 40px; }

  .name-bar {
    position: absolute; left: 0; top: 182px; width: 120px; height: 22px; background: var(--brand-blue);
  }
  .name-pill {
    position: absolute; left: 110px; top: 170px; width: 330px; height: 46px;
    background: var(--brand-blue); border-radius: 12px;
    color: var(--paper-text); font-weight: 300; font-size: 34px; line-height: 46px; padding-left: 18px;
  }
  .service-bar {
    position: absolute; left: 0; top: 236px; width: 340px; height: 16px; background: var(--brand-blue);
  }
  .service-pill {
    position: absolute; left: 325px; top: 229px; width: 140px; height: 30px;
    background: var(--brand-blue); border-radius: 10px;
    color: var(--paper-text); font-weight: 300; font-size: 18px; line-height: 30px; text-align: center;
  }

  .contact {
    position: absolute; left: 470px; top: 96px; padding-left: 14px;
    border-left: 3px solid var(--brand-blue);
    font-size: 13px; color: var(--ink); line-height: 22px;
  }
  .contact-line { display: flex; align-items: center; gap: 7px; }
  .contact-line svg { width: 13px; height: 13px; fill: var(--brand-blue); }

  .offer-list { position: absolute; list-style: none; font-size: 14px; color: var(--ink); line-height: 22px; }
  .offer-list li { display: flex; align-items: center; gap: 8px; }
  .offer-list li::before {
    content: ""; width: 8px; height: 8px; border-radius: 50%; background: var(--brand-blue); flex: none;
  }
  .offer-list--en { left: 480px; top: 222px; }
  .offer-list--fr { left: 70px; top: 290px; }
</style>
</head>
<body>
<main class="sheet">
  <section class="card card--front" aria-label="Recto de la carte">
    <div class="brand-lockup">
      <span class="brand-dot"></span>
      <span class="brand-name">58 BAINS</span>
    </div>
  </section>

  <section class="card card--back" aria-label="Verso de la carte">
    <div class="back-brand">
      <span class="brand-dot"></span>
      <span class="brand-name">58 BAINS</span>
    </div>

    <div class="contact">
      <div class="contact-line">
        <svg viewBox="0 0 24 24" aria-hidden="true"><path d="M6.6 10.8a15 15 0 0 0 6.6 6.6l2.2-2.2a1 1 0 0 1 1-.25 11.4 11.4 0 0 0 3.6.57 1 1 0 0 1 1 1V20a1 1 0 0 1-1 1A17 17 0 0 1 3 4a1 1 0 0 1 1-1h3.5a1 1 0 0 1 1 1c0 1.25.2 2.45.57 3.57a1 1 0 0 1-.25 1z"/></svg>
        <span>+33 (0)6 71 58 29 64</span>
      </div>
      <div class="contact-line">
        <svg viewBox="0 0 24 24" aria-hidden="true"><path d="M2 5h20v14H2z M4 7v.5l8 5 8-5V7l-8 5z" fill-rule="evenodd"/></svg>
        <span>lucimarch@examplemail.net</span>
      </div>
    </div>

    <span class="side-stripe side-stripe--one"></span>
    <span class="side-stripe side-stripe--two"></span>

    <span class="name-bar"></span>
    <h1 class="name-pill">Lucien Marchetti</h1>
    <span class="service-bar"></span>
    <p class="service-pill">Spas Services</p>

    <ul class="offer-list offer-list--en">
      <li>Custom maintenance contract.</li>
      <li>Water treatment, cleaning.</li>
      <li>Guidance.</li>
    </ul>

    <ul class="offer-list offer-list--fr">
      <li>Contrat d'entretien sur mesure.</li>
      <li>Traitement eau, nettoyage.</li>
      <li>Conseils.</li>
    </ul>
  </section>
</main>
</body>
</html>
```